Venture Capital Firm Needs Website Redesign

We need a bold revamp of our website (https://halverine.vc/)
which at the moment looks washed out. We want a crisp, fresh and unique look. Feel free to keep as much or as little content in the site. The only thing we need to keep is a team section. The site should convey a clear distinction between our 3 product lines: Venture Capital, Private Credit, and Crypto. Two versions of our logo are attached and they should not change. For design inspirations, we like http://www.9plm.com/ for a more simple site and for a more built out site we like http://bluetorch.com/

Updates
Industry/Entity Type
Investment
Coding
Coded - Design and coding required
Number of Pages Required
1 page
Font styles to use
Colors
Designer to choose colors to be used in the design.
Requirements
Must have
- - Clear distinction between our 3 product lines: Venture Capital, Private Credit
- - Team section

Nice to have
- Some really creative aspect like http://www.9plm.com/ has with the distinction between first, second, and third kind

```html
<!DOCTYPE html>
<html lang="en">
<head>
<meta charset="utf-8">
<title>Halverine</title>
<link rel="stylesheet" href="https://fonts.googleapis.com/css2?family=Open+Sans:wght@400;600;700&display=swap">
<style>
:root{
  --green:#7f9d4c;
  --green-dark:#6b8a3c;
  --ink:#333333;
  --muted:#777777;
  --light:#f1f1f1;
  --white:#ffffff;
  --hero-band:rgba(40,40,40,.55);
}
*{margin:0;padding:0;box-sizing:border-box}
html,body{width:763px;height:1200px;overflow:hidden;background:var(--white)}
body{font-family:'Open Sans',Arial,sans-serif;color:var(--ink);position:relative}
.site-header{position:absolute;top:0;left:0;width:763px;height:50px;display:flex;align-items:center;justify-content:space-between;padding:0 22px 0 18px}
.brand{font-weight:700;font-size:20px;color:var(--ink);letter-spacing:.5px}
.main-nav{display:flex;gap:20px;font-size:10px;font-weight:600}
.main-nav a{color:var(--ink);text-decoration:none;padding:3px 5px}
.main-nav a.active{background:var(--green);color:var(--white)}
.hero{position:absolute;top:50px;left:0;width:763px;height:290px;background:linear-gradient(135deg,#e9eaea 0%,#d9dbdc 50%,#eceded 100%)}
.hero-band{position:absolute;top:40px;left:0;width:763px;height:70px;background:var(--hero-band)}
.hero-title{position:absolute;top:46px;left:0;width:763px;text-align:center;color:var(--white);font-size:21px;font-weight:700;line-height:29px}
.hero-arrow{position:absolute;top:102px;width:16px;height:28px}
.hero-arrow.prev{left:10px}.hero-arrow.next{right:10px}
.btn{display:inline-block;background:var(--green);color:var(--white);font-size:9px;font-weight:600;padding:6px 16px;text-decoration:none}
.hero .btn{position:absolute;top:185px;left:340px}
.products{position:absolute;top:350px;left:0;width:763px;display:flex;justify-content:center;gap:40px}
.product{width:200px;text-align:center}
.product-icon{width:54px;height:54px;margin:0 auto 8px;display:block}
.product h3{font-size:12px;font-weight:700;margin-bottom:4px}
.product p{font-size:8px;color:var(--muted);line-height:12px;margin-bottom:6px}
.product .more{font-size:8px;font-weight:600;color:var(--ink)}
.product .more::after{content:"";display:block;width:26px;height:1px;background:var(--green);margin:3px auto 0}
.team{position:absolute;top:558px;left:0;width:763px;height:200px;background:linear-gradient(180deg,#8fa95f 0%,#7f9d4c 100%);color:var(--white);text-align:center}
.team h2{font-size:17px;font-weight:700;margin-top:30px}
.team p{font-size:11px;font-weight:600;width:520px;margin:8px auto 0;line-height:16px}
.values{display:flex;justify-content:center;gap:26px;margin-top:12px;font-size:13px;font-weight:600;letter-spacing:.5px}
.team .btn-light{display:inline-block;margin-top:18px;background:var(--white);color:var(--green-dark);font-size:9px;font-weight:600;padding:6px 18px}
.about{position:absolute;top:775px;left:0;width:763px;text-align:center}
.about h2{font-size:18px;font-weight:700;margin-bottom:6px}
.about h2::after{content:"";display:block;width:40px;height:2px;background:var(--green);margin:5px auto 0}
.about p{width:610px;margin:10px auto 12px;font-size:9px;line-height:14px;color:var(--muted)}
.site-footer{position:absolute;top:960px;left:0;width:763px;height:205px;background:var(--light)}
.footer-col{position:absolute;top:24px}
.footer-col h4{font-size:10px;font-weight:700;margin-bottom:12px}
.footer-col li{list-style:none;font-size:8.5px;line-height:15px;color:var(--ink)}
.footer-col p{font-size:8px;line-height:12px;color:var(--muted)}
.links{left:24px}.news{left:155px;width:140px}.contact{left:330px}
.news-input{width:124px;height:20px;border:1px solid #ccc;background:var(--white);font-size:7px;color:#999;padding:5px;margin:12px 0 8px}
.news .btn{padding:5px 12px;font-size:8px}
.contact strong{display:block;font-size:9px;margin-bottom:4px}
.footer-brand{position:absolute;top:90px;left:560px;width:150px;text-align:center;font-size:17px;font-weight:700;color:var(--ink)}
.copyright{position:absolute;top:1165px;left:0;width:763px;height:35px;background:var(--green);color:var(--white);font-size:8px;display:flex;align-items:center;justify-content:center}
</style>
</head>
<body>
<header class="site-header">
  <div class="brand">HALVERINE</div>
  <nav class="main-nav">
    <a class="active">Home</a><a>Venture Capital</a><a>Private Credit</a><a>Crypto</a><a>Team</a><a>Blog</a><a>Contact Us</a>
  </nav>
</header>

<section class="hero" role="img" aria-label="Light grey background of connected network lines and nodes">
  <div class="hero-band"></div>
  <h1 class="hero-title">Halverine Operates At The Intersection of Technology<br>And Novel Asset Classes.</h1>
  <svg class="hero-arrow prev" viewBox="0 0 16 28"><path d="M13 2 3 14l10 12" fill="none" stroke="#333" stroke-width="3"/></svg>
  <svg class="hero-arrow next" viewBox="0 0 16 28"><path d="M3 2l10 12L3 26" fill="none" stroke="#333" stroke-width="3"/></svg>
  <a class="btn">Learn More</a>
</section>

<section class="products">
  <article class="product">
    <svg class="product-icon" viewBox="0 0 54 54"><circle cx="27" cy="27" r="25" fill="none" stroke="#7f9d4c" stroke-width="2"/><path d="M16 34l8-8 6 5 9-11M33 20h6v6" fill="none" stroke="#555" stroke-width="2"/></svg>
    <h3>Venture Capital</h3>
    <p>We invest in early stage startups led by founders with passion and deep knowledge. [+]</p>
    <span class="more">Read More</span>
  </article>
  <article class="product">
    <svg class="product-icon" viewBox="0 0 54 54"><circle cx="27" cy="27" r="25" fill="none" stroke="#7f9d4c" stroke-width="2"/><rect x="15" y="19" width="24" height="16" rx="2" fill="none" stroke="#555" stroke-width="2"/><path d="M15 24h24" stroke="#555" stroke-width="2"/></svg>
    <h3>Private Credit</h3>
    <p>Our Private Credit arm provides capital to lending businesses focused on technology. [+]</p>
    <span class="more">Read More</span>
  </article>
  <article class="product">
    <svg class="product-icon" viewBox="0 0 54 54"><circle cx="27" cy="27" r="25" fill="none" stroke="#7f9d4c" stroke-width="2"/><circle cx="27" cy="27" r="10" fill="none" stroke="#555" stroke-width="2"/><circle cx="27" cy="27" r="5" fill="none" stroke="#555" stroke-width="1.5"/></svg>
    <h3>Crypto</h3>
    <p>Our Crypto fund tracks the top digital currencies weighted by market cap and settlement. [+]</p>
    <span class="more">Read More</span>
  </article>
</section>

<section class="team" role="img" aria-label="Green tinted grid of team member portraits">
  <h2>Our Team</h2>
  <p>Our Highly Skilled Financial Consultants Are People Who Personifies The Very Qualities That Have Made Us Successful.</p>
  <div class="values"><span>KNOWLEDGE</span><span>EXPERIENCE</span><span>ENTHUSIASM</span><span>DEDICATION</span></div>
  <span class="btn-light">Read More</span>
</section>

<section class="about">
  <h2>About Us</h2>
  <p>Halverine operates three businesses that bridge technology and finance. We invest in pre-seed venture capital, and build software for the companies we invest in. We manage direct private credit funds that provide private credit capital to alternative private credit platforms, enabling them to finance the loans they originate. We create crypto funds for individuals, RIAs and institutions to get simple and easy access to cryptocurrencies.</p>
  <a class="btn">Call for Today</a>
</section>

<footer class="site-footer">
  <div class="footer-col links">
    <h4>Quick Links</h4>
    <ul><li>Home</li><li>Venture Capital</li><li>Private Credit</li><li>Crypto</li><li>Team</li><li>Blog</li></ul>
  </div>
  <div class="footer-col news">
    <h4>Newsletter Signup</h4>
    <p>Short notes on our funds, portfolio news and market views, sent monthly.</p>
    <div class="news-input">Enter Your Email Here</div>
    <a class="btn">Subscribe</a>
  </div>
  <div class="footer-col contact">
    <h4>Contact Details</h4>
    <strong>Halverine</strong>
    <p>48 Larkspur Avenue, Suite 5<br>New York, NY 10010</p>
    <p style="margin-top:8px">555-0142</p>
    <p style="margin-top:6px">hello@halverine.vc</p>
  </div>
  <div class="footer-brand">HALVERINE</div>
</footer>
<div class="copyright">Copyright © 2019 Halverine , All Rights Reserved.</div>
</body>
</html>
```